Real Estate Company Looking for Business Card Designs for 3 Executives

Hello!
Thanks so much for considering our project! We are a real estate investment company located in Edmonton, Alberta called Bellhaven Group of Companies. We invest/develop both commercial and residential real estate and are looking to create 3 DOUBLE-SIDED business cards for 3 top executives in the company! (for some reason it won't let us select the double-sided option, but yes, the cards are double sided and would be happy to tip extra)

We have certain guidelines that we want our business cards to for sure follow - the back of the Business card has to be the Black Background Version of the Logo which has already been designed and linked as a file (first file). We want the entire back of the card to simply just be the black background logo. In terms of the front of the card, would like to see a smaller version of the white background logo (linked as the second file) in the top left hand corner - of course, feel free to get creative and we can make revisions together along the way! and Then after that, just text. We want the card to be sharp, clean, easy on the eyes and highly professional looking. We would like the card to include the Full name of the Company (Bellhaven Group of Companies), Name of the Person, Title, Phone, Email. If possible please provide the front part of the card for 3 people:

1) Bellhaven Group of Companies, Liora Quenby, Chief Financial Officer, 780-555-0142, lioraquenby@bellhavengroup.example

2) Bellhaven Group of Companies, Tobias Quenby, Chief Executive Officer, 780-555-0187, tobiasquenby@bellhavengroup.example

3) Bellhaven Group of Companies, Rui Delcourt, Chief Operations Officer, 587-555-0163, ruidelcourt@bellhavengroup.example

Thank you so much for considering our project & we look forward to seeing your designs!

```html
<!DOCTYPE html>
<html lang="en">
<head>
<meta charset="utf-8">
<title>Bellhaven Business Card</title>
<link rel="stylesheet" href="https://fonts.googleapis.com/css2?family=Karla:wght@400;500;700&display=swap">
<style>
  :root {
    --page-bg: #1b1b1c;
    --card-bg: #2a2a2b;
    --card-edge: #333335;
    --ink-white: #f4f4f4;
    --ink-soft: #d8d8d8;
    --gloss: #4a4a4c;
    --tree-light: #eeeeee;
  }
  * { margin: 0; padding: 0; box-sizing: border-box; }
  html, body {
    width: 1200px; height: 874px; overflow: hidden;
    background: var(--page-bg);
    font-family: "Karla", Arial, sans-serif;
  }
  .stage {
    position: relative; width: 1200px; height: 874px;
  }
  .card {
    position: absolute; left: 290px; width: 620px; height: 354px;
    background: var(--card-bg);
    border: 1px solid var(--card-edge);
    box-shadow: 0 12px 30px rgba(0,0,0,0.55);
    overflow: hidden;
  }
  .card-back { top: 68px; }
  .card-front { top: 452px; }

  /* Back: wordmark centred */
  .back-mark {
    position: absolute; inset: 0;
    display: flex; flex-direction: column; align-items: center; justify-content: center;
    gap: 14px;
  }
  .back-mark .dot {
    width: 14px; height: 14px; background: var(--gloss);
  }
  .back-mark .wordmark {
    font-weight: 500; font-size: 34px; letter-spacing: 0.42em;
    color: var(--gloss); padding-left: 0.42em;
  }

  /* Front */
  .front-brand {
    position: absolute; left: 40px; top: 44px;
    display: flex; align-items: center; gap: 12px;
  }
  .front-brand .dot { width: 12px; height: 12px; background: var(--ink-white); }
  .front-brand .wordmark {
    font-weight: 500; font-size: 26px; letter-spacing: 0.32em; color: var(--ink-white);
  }
  .company-name {
    position: absolute; left: 64px; top: 84px;
    font-weight: 700; font-size: 11px; letter-spacing: 0.08em;
    text-transform: uppercase; color: var(--ink-soft);
  }
  .person { position: absolute; left: 40px; top: 150px; color: var(--ink-white); }
  .person-name {
    font-weight: 700; font-size: 21px; letter-spacing: 0.06em; text-transform: uppercase;
  }
  .person-title { font-size: 15px; color: var(--ink-soft); margin-top: 2px; }
  .contacts { list-style: none; margin-top: 16px; }
  .contacts li {
    display: flex; align-items: center; gap: 10px;
    font-size: 15px; color: var(--ink-white); line-height: 24px;
  }
  .contacts svg { width: 12px; height: 12px; fill: var(--ink-soft); flex: none; }

  .tree-art {
    position: absolute; left: 430px; top: 40px; width: 130px; height: 314px;
    background: linear-gradient(180deg, rgba(238,238,238,0.35) 0%, var(--tree-light) 100%);
  }
</style>
</head>
<body>
<main class="stage">
  <section class="card card-back" aria-label="Card back">
    <div class="back-mark">
      <span class="dot"></span>
      <span class="wordmark">BELLHAVEN</span>
    </div>
  </section>

  <section class="card card-front" aria-label="Card front">
    <div class="front-brand">
      <span class="dot"></span>
      <span class="wordmark">BELLHAVEN</span>
    </div>
    <p class="company-name">Bellhaven Group of Companies</p>

    <div class="person">
      <h1 class="person-name">Liora Quenby</h1>
      <p class="person-title">Chief Financial Officer</p>
      <ul class="contacts">
        <li>
          <svg viewBox="0 0 24 24" aria-hidden="true"><path d="M6.6 10.8a15.1 15.1 0 0 0 6.6 6.6l2.2-2.2c.3-.3.7-.4 1-.2 1.1.4 2.3.6 3.6.6.6 0 1 .4 1 1V20c0 .6-.4 1-1 1A17 17 0 0 1 3 4c0-.6.4-1 1-1h3.5c.6 0 1 .4 1 1 0 1.3.2 2.5.6 3.6.1.3 0 .7-.2 1z"/></svg>
          780-555-0142
        </li>
        <li>
          <svg viewBox="0 0 24 24" aria-hidden="true"><path d="M2 5h20v14H2z M2 5l10 8 10-8" /></svg>
          lioraquenby@bellhavengroup.example
        </li>
        <li>
          <svg viewBox="0 0 24 24" aria-hidden="true"><circle cx="12" cy="12" r="10"/></svg>
          bellhavengroup.example
        </li>
      </ul>
    </div>

    <div class="tree-art" role="img" aria-label="White illustration of two tall pine tree trunks rising from the bottom edge"></div>
  </section>
</main>
</body>
</html>
```